Business Card Design for Occupational Medicine Start Up Company

We need to design a professional business card. We are a healthcare company providing occupational medicine services to blue collar industries. We are professional, efficient and high quality service providers.

Target Market(s)

Blue Collar Industry: Shipbuilding, Ports, Trucking Companies; The Executives and Safety Officers for these companies

Industry/Entity Type

Healthcare

Contact Information for Business Card

Logo, Name, Title, Email, Phone

Other font styles liked:
• Please match our Brand Guide

Requirements
Must have
• Our Company Colors and Logo

```html
<!DOCTYPE html>
<html lang="en">
<head>
<meta charset="utf-8">
<title>CrewSteady Business Card</title>
<link rel="stylesheet" href="https://fonts.googleapis.com/css2?family=Roboto:wght@400;700;900&display=swap">
<style>
  :root {
    --stage: #1b1b1b;
    --card-dark: #0e0e0e;
    --card-dark-sheen: #2a2a2a;
    --paper: #ffffff;
    --navy: #26357f;
    --orange: #f5a93b;
    --sky: #29a8e0;
    --ink: #1d1d1f;
  }
  * { box-sizing: border-box; margin: 0; padding: 0; }
  html, body { width: 1200px; height: 900px; overflow: hidden; }
  body {
    background: var(--stage);
    font-family: "Roboto", Arial, sans-serif;
    position: relative;
  }
  .card {
    position: absolute;
    left: 270px;
    width: 660px;
    height: 377px;
    overflow: hidden;
  }
  .card-back { top: 40px; background: var(--card-dark); }
  .card-front { top: 473px; background: var(--paper); }

  .back-texture {
    position: absolute; inset: 0;
    background: linear-gradient(135deg, var(--card-dark) 0%, var(--card-dark-sheen) 55%, #3a3a3a 75%, var(--card-dark) 100%);
  }
  .back-mark {
    position: absolute; right: 110px; bottom: 80px;
    width: 34px; height: 34px; border-radius: 50%;
    background: var(--sky);
  }

  .brand {
    position: absolute; left: 70px; top: 70px;
    display: flex; align-items: center; gap: 14px;
  }
  .brand-dot { width: 40px; height: 40px; border-radius: 50%; background: var(--sky); }
  .brand-name {
    font-weight: 700; font-size: 36px; letter-spacing: 2px; color: var(--navy);
  }

  .contact {
    position: absolute; left: 52px; top: 236px;
    list-style: none; font-size: 16px; color: var(--ink); line-height: 24px;
  }
  .contact li { display: flex; align-items: center; gap: 6px; }
  .contact svg { width: 13px; height: 13px; fill: var(--navy); }

  .person {
    position: absolute; right: 62px; top: 198px; text-align: right;
  }
  .person-name { font-weight: 900; font-size: 29px; color: var(--navy); letter-spacing: 0.5px; }
  .person-title { font-size: 16px; color: var(--ink); margin-top: 10px; }
  .name-tab {
    position: absolute; right: 0; top: 206px; width: 30px; height: 48px; background: var(--navy);
  }
  .card-art { position: absolute; inset: 0; }
</style>
</head>
<body>
  <section class="card card-back">
    <div class="back-texture" role="img" aria-label="Dark embossed repeating brand pattern"></div>
    <div class="back-mark"></div>
  </section>

  <section class="card card-front">
    <svg class="card-art" viewBox="0 0 660 377" width="660" height="377" aria-hidden="true">
      <line x1="90" y1="226" x2="560" y2="226" stroke="var(--orange)" stroke-width="2"/>
      <path d="M0 318 H360 C380 318 390 326 400 330 H0 Z" fill="var(--orange)"/>
      <path d="M0 336 H400 C430 336 440 312 470 312 H660 V377 H0 Z" fill="var(--navy)"/>
    </svg>

    <div class="brand">
      <span class="brand-dot"></span>
      <span class="brand-name">CREWSTEADY</span>
    </div>

    <ul class="contact">
      <li><svg viewBox="0 0 16 16"><path d="M4 1l3 3-2 2c1 2 3 4 5 5l2-2 3 3-2 3C7 15 1 9 1 3z"/></svg>(480)555 0142</li>
      <li><svg viewBox="0 0 16 16"><path d="M1 3h14v10H1z M1 3l7 6 7-6" fill="none" stroke="var(--navy)" stroke-width="1.6"/></svg>info@crewsteady.com</li>
      <li><svg viewBox="0 0 16 16"><circle cx="8" cy="8" r="6.5" fill="none" stroke="var(--navy)" stroke-width="1.4"/><path d="M1.5 8h13M8 1.5v13" stroke="var(--navy)" stroke-width="1.2"/></svg>www.crewsteady.com</li>
    </ul>

    <div class="person">
      <div class="person-name">MARK DELANEY</div>
      <div class="person-title">Director</div>
    </div>
    <div class="name-tab"></div>
  </section>
</body>
</html>
```